FinTech company looking to revamp and expand client-facing interface for our financial models

Pellworth Engines currently has a very simple website that allows clients to interact with our financial models. We are looking to completely redesign the current site and add several extra pages to provide extra functionality. We want the design to have a modern, slick feel, that will work on both a desktop or a tablet. It should be straightforward for clients to move between different pages at any time, and clear from the layout how to interact with the more advanced features. We have included screenshots of existing pages in the attached design brief, as well as sketches of the functionality required by the new pages, but can't provide a direct link to the current site.
Target Market(s)
Professional investors that will be paying to access the interface
Industry/Entity Type
Finance
Number of Pages Required
4 page
Colors
Designer to choose colors to be used in the design.
Look and feel
Each slider illustrates characteristics of the customer's brand and the style your logo design should communicate.

```html
<!DOCTYPE html>
<html lang="en">
<head>
<meta charset="utf-8">
<title>QVANTA – Pellworth Engines model interface</title>
<link rel="stylesheet" href="https://fonts.googleapis.com/css2?family=Open+Sans:wght@400;600;700&display=swap">
<style>
:root{
  --teal:#2fae97;
  --teal-soft:#e2f2ee;
  --ink:#1b1b1b;
  --muted:#9a9a9a;
  --white:#ffffff;
  --line:#ececec;
  --page-top:#e6e6e6;
  --page-bottom:#f8f8f8;
  --panel-grey:#efefef;
  --series-gold:#b8b43a;
  --series-blue:#3a70b0;
  --series-green:#4a9a3a;
}
*{box-sizing:border-box;margin:0;padding:0}
html,body{width:1135px;height:1200px;overflow:hidden}
body{
  font-family:"Open Sans",sans-serif;color:var(--ink);position:relative;
  background:linear-gradient(180deg,var(--page-top) 0,var(--page-bottom) 420px,var(--page-bottom) 100%);
}
.topbar{position:absolute;left:0;top:0;width:1135px;height:52px;background:var(--white);box-shadow:0 2px 10px rgba(0,0,0,.06)}
.brand{position:absolute;left:63px;top:0;line-height:52px;font-weight:700;font-size:17px;letter-spacing:.2px}
.range-tab{position:absolute;top:0;height:52px;line-height:52px;text-align:center;font-size:13px;font-weight:700;border-right:1px solid var(--line)}
.range-tab.active{background:var(--teal);color:var(--white);border-right:none}
.nav-item{position:absolute;top:0;height:52px;display:flex;align-items:center;justify-content:center;gap:7px;font-size:11.5px;font-weight:700;border-left:1px solid var(--line)}
.nav-item svg{width:20px;height:20px}
.section-label{position:absolute;left:61px;width:284px;height:35px;line-height:35px;text-align:center;background:var(--muted);color:var(--white);font-weight:600;font-size:15px;border-radius:3px}
.table{position:absolute;left:61px;width:1013px;background:var(--white);border-radius:4px;box-shadow:0 2px 8px rgba(0,0,0,.06);overflow:hidden}
.row{display:flex;height:59px;align-items:center}
.row.tint{background:var(--teal-soft)}
.cell{height:100%;display:flex;align-items:center;justify-content:center;font-size:15.5px;border-right:1px solid var(--line)}
.cell:last-child{border-right:none}
.head{height:61px}
.head .cell{font-weight:600;color:var(--white);background:var(--teal);border-right:1px solid rgba(255,255,255,.18)}
.head .id-col{background:var(--ink)}
.id-col{width:384px}
.stat-col{width:157px}
.stat-col:last-child{flex:1}
.grid-col{flex:1}
.collapse-btn{position:absolute;left:1048px;top:428px;width:27px;height:27px;border-radius:50%;background:#3b3b3b;border:2px solid #cfcfcf;box-shadow:0 0 0 1px #888}
.collapse-btn svg{width:23px;height:23px}
.chart-panel{position:absolute;left:61px;top:760px;width:1013px;height:371px;background:var(--white);border-radius:4px;box-shadow:0 2px 8px rgba(0,0,0,.06);overflow:hidden}
.chart-tabs{position:absolute;left:0;top:0;width:100%;height:74px;background:var(--panel-grey)}
.chart-tab{position:absolute;top:43px;height:31px;line-height:31px;text-align:center;font-size:15px;font-weight:600}
.chart-tab.active{background:var(--teal);color:var(--white);font-size:15px}
.chart-tab.plain{background:var(--white)}
.chart-tab.hover{background:#f6f6f6;top:36px;height:38px;line-height:32px;color:#555}
.plot{position:absolute;left:87px;top:864px;width:960px;height:227px}
.pointer{position:absolute;left:540px;top:818px;width:25px;height:30px}
</style>
</head>
<body>

<header class="topbar">
  <div class="brand">QVANTA</div>
  <div class="range-tab active" style="left:170px;width:79px">250D</div>
  <div class="range-tab" style="left:249px;width:78px">83D</div>
  <div class="range-tab" style="left:327px;width:79px">42D</div>
  <div class="nav-item" style="left:525px;width:122px">
    <svg viewBox="0 0 20 20"><path d="M2 10 10 3l8 7M5 8v9h4v-5h2v5h4V8" fill="none" stroke="#1b1b1b" stroke-width="2" stroke-linejoin="round"/></svg>MODELS</div>
  <div class="nav-item" style="left:647px;width:154px">
    <svg viewBox="0 0 20 20"><g fill="#1b1b1b"><circle cx="10" cy="10" r="2.2"/><circle cx="10" cy="3" r="1.4"/><circle cx="10" cy="17" r="1.4"/><circle cx="3" cy="10" r="1.4"/><circle cx="17" cy="10" r="1.4"/><circle cx="5" cy="5" r="1.4"/><circle cx="15" cy="15" r="1.4"/><circle cx="15" cy="5" r="1.4"/><circle cx="5" cy="15" r="1.4"/></g><circle cx="10" cy="10" r="5" fill="none" stroke="#1b1b1b" stroke-width="1" stroke-dasharray="1.5 1.5"/></svg>SENSITIVITIES</div>
  <div class="nav-item" style="left:801px;width:140px">
    <svg viewBox="0 0 20 20"><g fill="none" stroke="#1b1b1b" stroke-width="1.6"><circle cx="5.5" cy="5.5" r="3.5"/><circle cx="14.5" cy="5.5" r="3.5"/><circle cx="5.5" cy="14.5" r="3.5"/><circle cx="14.5" cy="14.5" r="3.5"/></g></svg>PORTFOLIO</div>
  <div class="nav-item" style="left:941px;width:133px;border-right:1px solid var(--line)">
    <svg viewBox="0 0 20 20"><rect x="2" y="3" width="16" height="14" fill="none" stroke="#1b1b1b" stroke-width="1.6"/><path d="M4 14l4-5 3 3 5-6" fill="none" stroke="#1b1b1b" stroke-width="1.6"/></svg>BACKTEST</div>
</header>

<div class="section-label" style="top:87px">Number of Selected Factors : 3</div>
<section class="table" style="top:135px">
  <div class="row head"><div class="cell id-col">ID&nbsp;<svg width="10" height="10" viewBox="0 0 10 10"><path d="M2 3.5 5 6.5 8 3.5" fill="none" stroke="#fff" stroke-width="1.5"/></svg></div><div class="cell stat-col">Stat 1</div><div class="cell stat-col">Stat 2</div><div class="cell stat-col">Stat 3</div><div class="cell stat-col">Stat 4</div></div>
  <div class="row"><div class="cell id-col">Factor 1</div><div class="cell stat-col">-1.4</div><div class="cell stat-col">0.094</div><div class="cell stat-col">6.1</div><div class="cell stat-col">100</div></div>
  <div class="row tint"><div class="cell id-col">Factor 2</div><div class="cell stat-col">2.8</div><div class="cell stat-col">0.085</div><div class="cell stat-col">3.1</div><div class="cell stat-col">0.7</div></div>
  <div class="row"><div class="cell id-col">Factor 3</div><div class="cell stat-col">-3.7</div><div class="cell stat-col">2.7</div><div class="cell stat-col">-7.2</div><div class="cell stat-col">100</div></div>
</section>

<div class="section-label" style="top:423px">Unselected Factors</div>
<div class="collapse-btn"><svg viewBox="0 0 23 23"><path d="M6 14l5.5-5.5L17 14" fill="none" stroke="#fff" stroke-width="2.4"/></svg></div>
<section class="table" style="top:471px">
  <div class="row tint"><div class="cell grid-col">Factor</div><div class="cell grid-col">Factor</div><div class="cell grid-col">Factor</div><div class="cell grid-col">Factor</div><div class="cell grid-col">Factor</div></div>
  <div class="row"><div class="cell grid-col">Factor</div><div class="cell grid-col">Factor</div><div class="cell grid-col">Factor</div><div class="cell grid-col">Factor</div><div class="cell grid-col">Factor</div></div>
  <div class="row tint"><div class="cell grid-col">Factor</div><div class="cell grid-col">Factor</div><div class="cell grid-col">Factor</div><div class="cell grid-col">Factor</div><div class="cell grid-col">Factor</div></div>
  <div class="row"><div class="cell grid-col">Factor</div><div class="cell grid-col">Factor</div><div class="cell grid-col">Factor</div><div class="cell grid-col">Factor</div><div class="cell grid-col">Factor</div></div>
</section>

<section class="chart-panel">
  <div class="chart-tabs">
    <div class="chart-tab active" style="left:48px;width:135px">Chart</div>
    <div class="chart-tab plain" style="left:188px;width:78px">#1</div>
    <div class="chart-tab" style="left:280px;width:60px">#2</div>
    <div class="chart-tab" style="left:363px;width:60px">#3</div>
    <div class="chart-tab hover" style="left:437px;width:78px">#4</div>
  </div>
</section>

<svg class="pointer" viewBox="0 0 25 30"><path d="M8 2c1.5 0 2 1 2 2v9l1-1c1-1 3 0 3 1 1-1 3 0 3 1 1-.5 3 0 3 1.5V22c0 3-2 6-6 6h-3c-2 0-3-1-4-2l-5-7c-1-1.5 1-3 2.5-1.5L6 19V4c0-1 .5-2 2-2z" fill="#fff" stroke="#1b1b1b" stroke-width="1.4" stroke-linejoin="round"/></svg>

<svg class="plot" viewBox="100 990 1100 260" role="img" aria-label="Scatter chart of factor scores from July 2018 to July 2019">
  <g stroke="#ededed" stroke-width="1">
    <line x1="155" y1="1018" x2="1075" y2="1018"/><line x1="155" y1="1055" x2="1075" y2="1055"/><line x1="155" y1="1092" x2="1075" y2="1092"/><line x1="155" y1="1130" x2="1075" y2="1130"/><line x1="155" y1="1167" x2="1075" y2="1167"/>
    <line x1="182" y1="1003" x2="182" y2="1205"/><line x1="325" y1="1003" x2="325" y2="1205"/><line x1="465" y1="1003" x2="465" y2="1205"/><line x1="606" y1="1003" x2="606" y2="1205"/><line x1="742" y1="1003" x2="742" y2="1205"/><line x1="883" y1="1003" x2="883" y2="1205"/><line x1="1023" y1="1003" x2="1023" y2="1205"/>
  </g>
  <line x1="155" y1="1205" x2="1075" y2="1205" stroke="#999" stroke-width="1.2"/>
  <g font-family="Open Sans, sans-serif" font-size="12" fill="#666" text-anchor="end">
    <text x="150" y="1022">100</text><text x="150" y="1059">80</text><text x="150" y="1096">60</text><text x="150" y="1134">40</text><text x="150" y="1171">20</text><text x="150" y="1209">0</text>
  </g>
  <g font-family="Open Sans, sans-serif" font-size="12" fill="#666" text-anchor="middle">
    <text x="182" y="1230">Jul 2018</text><text x="325" y="1230">Sep 2018</text><text x="465" y="1230">Nov 2018</text><text x="606" y="1230">Jan 2019</text><text x="742" y="1230">Mar 2019</text><text x="883" y="1230">May 2019</text><text x="1023" y="1230">Jul 2019</text>
  </g>

  <g stroke="var(--series-gold)" stroke-width="7" stroke-linecap="round" stroke-dasharray="0 7">
    <line x1="200" y1="1018" x2="284" y2="1018"/><line x1="760" y1="1021" x2="1000" y2="1021"/>
  </g>
  <g fill="var(--series-gold)">
    <circle cx="285" cy="1022" r="3.5"/><circle cx="290" cy="1031" r="3.5"/><circle cx="297" cy="1033" r="3.5"/><circle cx="303" cy="1025" r="3.5"/><circle cx="310" cy="1021" r="3.5"/><circle cx="318" cy="1025" r="3.5"/><circle cx="325" cy="1024" r="3.5"/><circle cx="333" cy="1028" r="3.5"/>
    <circle cx="337" cy="1083" r="3.5"/><circle cx="340" cy="1113" r="3.5"/><circle cx="348" cy="1118" r="3.5"/><circle cx="352" cy="1097" r="3.5"/><circle cx="355" cy="1117" r="3.5"/><circle cx="347" cy="1133" r="3.5"/><circle cx="360" cy="1133" r="3.5"/><circle cx="365" cy="1135" r="3.5"/><circle cx="368" cy="1113" r="3.5"/><circle cx="372" cy="1110" r="3.5"/><circle cx="376" cy="1122" r="3.5"/><circle cx="380" cy="1078" r="3.5"/><circle cx="384" cy="1083" r="3.5"/><circle cx="388" cy="1057" r="3.5"/><circle cx="394" cy="1048" r="3.5"/><circle cx="398" cy="1046" r="3.5"/><circle cx="400" cy="1022" r="3.5"/><circle cx="408" cy="1023" r="3.5"/><circle cx="413" cy="1080" r="3.5"/><circle cx="415" cy="1093" r="3.5"/><circle cx="420" cy="1104" r="3.5"/><circle cx="425" cy="1110" r="3.5"/><circle cx="430" cy="1101" r="3.5"/>
    <circle cx="435" cy="1175" r="3.5"/><circle cx="440" cy="1170" r="3.5"/><circle cx="445" cy="1183" r="3.5"/><circle cx="448" cy="1155" r="3.5"/><circle cx="452" cy="1168" r="3.5"/><circle cx="456" cy="1189" r="3.5"/><circle cx="460" cy="1175" r="3.5"/><circle cx="463" cy="1185" r="3.5"/><circle cx="468" cy="1198" r="3.5"/><circle cx="473" cy="1192" r="3.5"/><circle cx="478" cy="1188" r="3.5"/><circle cx="483" cy="1195" r="3.5"/><circle cx="488" cy="1185" r="3.5"/><circle cx="493" cy="1180" r="3.5"/><circle cx="497" cy="1152" r="3.5"/><circle cx="500" cy="1170" r="3.5"/><circle cx="507" cy="1146" r="3.5"/><circle cx="512" cy="1140" r="3.5"/><circle cx="518" cy="1148" r="3.5"/><circle cx="523" cy="1144" r="3.5"/><circle cx="527" cy="1123" r="3.5"/><circle cx="530" cy="1103" r="3.5"/><circle cx="533" cy="1090" r="3.5"/><circle cx="538" cy="1093" r="3.5"/>
    <circle cx="541" cy="1020" r="3.5"/><circle cx="548" cy="1021" r="3.5"/><circle cx="553" cy="1025" r="3.5"/><circle cx="560" cy="1023" r="3.5"/><circle cx="574" cy="1038" r="3.5"/>
    <circle cx="578" cy="1195" r="3.5"/><circle cx="582" cy="1196" r="3.5"/><circle cx="592" cy="1190" r="3.5"/><circle cx="597" cy="1194" r="3.5"/><circle cx="605" cy="1185" r="3.5"/><circle cx="612" cy="1180" r="3.5"/><circle cx="620" cy="1178" r="3.5"/><circle cx="625" cy="1188" r="3.5"/><circle cx="630" cy="1182" r="3.5"/><circle cx="636" cy="1194" r="3.5"/><circle cx="640" cy="1186" r="3.5"/>
    <circle cx="652" cy="1153" r="3.5"/><circle cx="655" cy="1152" r="3.5"/><circle cx="658" cy="1118" r="3.5"/><circle cx="660" cy="1133" r="3.5"/><circle cx="655" cy="1082" r="3.5"/><circle cx="668" cy="1081" r="3.5"/><circle cx="670" cy="1045" r="3.5"/><circle cx="674" cy="1039" r="3.5"/><circle cx="688" cy="1040" r="3.5"/><circle cx="691" cy="1094" r="3.5"/><circle cx="694" cy="1161" r="3.5"/><circle cx="700" cy="1165" r="3.5"/><circle cx="703" cy="1175" r="3.5"/><circle cx="705" cy="1040" r="3.5"/><circle cx="708" cy="1050" r="3.5"/><circle cx="707" cy="1075" r="3.5"/><circle cx="713" cy="1058" r="3.5"/><circle cx="718" cy="1075" r="3.5"/><circle cx="721" cy="1118" r="3.5"/><circle cx="723" cy="1027" r="3.5"/><circle cx="733" cy="1045" r="3.5"/><circle cx="736" cy="1032" r="3.5"/><circle cx="740" cy="1036" r="3.5"/><circle cx="745" cy="1033" r="3.5"/><circle cx="752" cy="1030" r="3.5"/><circle cx="756" cy="1028" r="3.5"/>
  </g>

  <g stroke="var(--series-blue)" stroke-width="7" stroke-linecap="round" stroke-dasharray="0 7">
    <line x1="590" y1="1018" x2="1025" y2="1018"/>
  </g>
  <g fill="var(--series-blue)">
    <circle cx="203" cy="1083" r="3.5"/><circle cx="205" cy="1030" r="3.5"/><circle cx="208" cy="1022" r="3.5"/><circle cx="215" cy="1025" r="3.5"/><circle cx="220" cy="1028" r="3.5"/><circle cx="217" cy="1100" r="3.5"/><circle cx="225" cy="1133" r="3.5"/><circle cx="230" cy="1118" r="3.5"/><circle cx="234" cy="1143" r="3.5"/><circle cx="238" cy="1160" r="3.5"/><circle cx="240" cy="1140" r="3.5"/><circle cx="245" cy="1135" r="3.5"/><circle cx="250" cy="1125" r="3.5"/><circle cx="255" cy="1095" r="3.5"/><circle cx="258" cy="1120" r="3.5"/><circle cx="262" cy="1135" r="3.5"/><circle cx="265" cy="1115" r="3.5"/><circle cx="270" cy="1098" r="3.5"/><circle cx="270" cy="1118" r="3.5"/><circle cx="275" cy="1158" r="3.5"/><circle cx="280" cy="1160" r="3.5"/><circle cx="285" cy="1120" r="3.5"/><circle cx="288" cy="1135" r="3.5"/><circle cx="292" cy="1130" r="3.5"/><circle cx="297" cy="1150" r="3.5"/><circle cx="300" cy="1160" r="3.5"/><circle cx="305" cy="1155" r="3.5"/><circle cx="310" cy="1162" r="3.5"/><circle cx="312" cy="1148" r="3.5"/><circle cx="318" cy="1160" r="3.5"/><circle cx="322" cy="1153" r="3.5"/><circle cx="330" cy="1165" r="3.5"/>
    <circle cx="335" cy="1185" r="3.5"/><circle cx="340" cy="1185" r="3.5"/><circle cx="345" cy="1180" r="3.5"/><circle cx="350" cy="1178" r="3.5"/><circle cx="355" cy="1187" r="3.5"/><circle cx="360" cy="1180" r="3.5"/><circle cx="365" cy="1185" r="3.5"/><circle cx="370" cy="1175" r="3.5"/><circle cx="375" cy="1178" r="3.5"/><circle cx="380" cy="1160" r="3.5"/><circle cx="385" cy="1152" r="3.5"/><circle cx="390" cy="1165" r="3.5"/><circle cx="395" cy="1145" r="3.5"/><circle cx="400" cy="1150" r="3.5"/><circle cx="403" cy="1163" r="3.5"/><circle cx="408" cy="1170" r="3.5"/><circle cx="412" cy="1160" r="3.5"/><circle cx="416" cy="1148" r="3.5"/><circle cx="420" cy="1168" r="3.5"/><circle cx="425" cy="1165" r="3.5"/><circle cx="430" cy="1160" r="3.5"/><circle cx="435" cy="1200" r="3.5"/><circle cx="440" cy="1195" r="3.5"/><circle cx="445" cy="1185" r="3.5"/><circle cx="450" cy="1180" r="3.5"/><circle cx="455" cy="1165" r="3.5"/><circle cx="460" cy="1147" r="3.5"/>
    <circle cx="465" cy="1075" r="3.5"/><circle cx="470" cy="1047" r="3.5"/><circle cx="475" cy="1040" r="3.5"/><circle cx="478" cy="1030" r="3.5"/><circle cx="480" cy="1055" r="3.5"/><circle cx="485" cy="1040" r="3.5"/><circle cx="490" cy="1055" r="3.5"/>
    <circle cx="495" cy="1180" r="3.5"/><circle cx="498" cy="1170" r="3.5"/><circle cx="503" cy="1165" r="3.5"/><circle cx="508" cy="1155" r="3.5"/><circle cx="513" cy="1158" r="3.5"/><circle cx="518" cy="1152" r="3.5"/><circle cx="522" cy="1168" r="3.5"/><circle cx="528" cy="1140" r="3.5"/><circle cx="533" cy="1125" r="3.5"/><circle cx="540" cy="1125" r="3.5"/>
    <circle cx="543" cy="1040" r="3.5"/><circle cx="547" cy="1035" r="3.5"/><circle cx="555" cy="1025" r="3.5"/><circle cx="563" cy="1032" r="3.5"/><circle cx="570" cy="1028" r="3.5"/>
  </g>
  <g fill="var(--series-green)">
    <circle cx="1000" cy="1201" r="3.5"/><circle cx="1005" cy="1201" r="3.5"/><circle cx="1010" cy="1201" r="3.5"/>
  </g>

  <g class="legend">
    <text x="1132" y="1020" font-family="Open Sans, sans-serif" font-size="11" fill="#444">Names</text>
    <circle cx="1114" cy="1016" r="3.2" fill="#8fb1d6"/><circle cx="1114" cy="1035" r="3.2" fill="#f4b27a"/><circle cx="1114" cy="1053" r="3.2" fill="#3f9a3a"/><circle cx="1114" cy="1072" r="3.2" fill="#e07a7a"/><circle cx="1114" cy="1091" r="3.2" fill="#c79ad8"/><circle cx="1114" cy="1109" r="3.2" fill="#b39a94"/><circle cx="1114" cy="1128" r="3.2" fill="#eaa8d2"/><circle cx="1114" cy="1147" r="3.2" fill="#bdbdbd"/><circle cx="1114" cy="1165" r="3.2" fill="#b8b43a"/><circle cx="1114" cy="1184" r="3.2" fill="#8fd6e0"/><circle cx="1114" cy="1202" r="3.2" fill="#3a70b0"/>
  </g>
</svg>

</body>
</html>
```